Media Services Start-up -- Corporate Website and Logo Design. Inspiration required!

We need a logo design and corporate website design, including coding, for our start-up business.
Vennatra’s value proposition is based on bringing together media content from a vast number of geographies globally, adding human and AI curation, translation and editing, and delivering the content using tailored customer interfaces. On the one hand, the business brings together media coverage from all over the world, and on the other it brings together content, human skills and technology to deliver a supreme customer experience.
Vennatra is a B2B media monitoring and analytics business with emphasis on global customers. Vennatra's service offering is centred around sourcing media content from different markets, processing, storing and delivering the content and insights derived from it using an online platform / mobile app.
The messaging we want to create through the logo is:
- Global scope
- Speed of delivery
- Cost-efficiency
- Multi-lingual
- Tailor-made
- Trustworthy
Target Market(s)
Business to business, PR / Communications, Media, Marketing
Logo Text
Vennatra
Coding
Coded - Design and coding required
Number of Pages Required
5+ page
Font styles to use
Other font styles liked:
- See Design Brief for details
Colors
Designer to choose colors to be used in the design.

```html
<!DOCTYPE html>
<html lang="en">
<head>
<meta charset="utf-8">
<title>Our Approach – Vennatra Media Intelligence</title>
<link href="https://fonts.googleapis.com/css2?family=Roboto:wght@400;500&family=Roboto+Condensed:wght@700&display=swap" rel="stylesheet">
<style>
:root{
  --bg:#0b0b0b;
  --header:#151515;
  --teal:#3ab5a3;
  --white:#ffffff;
  --band-light:rgba(70,70,70,.72);
  --band-dark:rgba(34,34,34,.92);
  --text-soft:#e6e6e6;
}
*{margin:0;padding:0;box-sizing:border-box}
html,body{width:1200px;height:839px;overflow:hidden;background:var(--bg)}
body{position:relative;font-family:'Roboto',sans-serif;color:var(--white)}
.abs{position:absolute}
.hero-visual{left:0;top:85px;width:1200px;height:683px;
  background:radial-gradient(circle at 600px 260px,#4a4a4a 0,#2c2c2c 180px,#161616 420px,#0d0d0d 700px)}
.site-header{left:0;top:0;width:1200px;height:85px;background:var(--header)}
.brand{left:141px;top:16px;display:flex;align-items:center;gap:12px}
.brand-dot{width:46px;height:46px;border-radius:50%;background:var(--teal)}
.brand-name{font-size:15px;line-height:17px;font-weight:400;letter-spacing:.3px}
.contact{top:13px;display:flex;align-items:center;gap:9px;font-size:14px}
.contact-icon{width:27px;height:27px;border:1.4px solid var(--white);border-radius:50%;display:flex;align-items:center;justify-content:center}
.nav a{position:absolute;top:54px;font-size:14px;color:var(--white);text-decoration:none}
.nav a.active{color:var(--teal);font-weight:500}
.sign-in{left:974px;top:49px;width:85px;height:29px;background:var(--teal);font-size:15px;display:flex;align-items:center;justify-content:center;letter-spacing:.5px}
.page-title{left:0;width:1200px;top:134px;text-align:center;font-family:'Roboto Condensed',sans-serif;font-size:33px;font-weight:700}
.intro{left:180px;width:840px;top:192px;text-align:center;font-family:'Roboto Condensed',sans-serif;font-weight:700;font-size:14px;line-height:23px}
.band{left:0;width:1200px}
.band.light{background:var(--band-light)}
.band.dark{background:var(--band-dark)}
.row-label{left:143px;color:var(--teal);font-size:21px;line-height:27px}
.item{text-align:center;font-size:15px;line-height:20px;color:var(--text-soft);width:180px}
.item svg{display:block;margin:0 auto 24px}
.list{font-size:15px;line-height:23px;color:var(--text-soft)}
.site-footer{left:0;top:805px;width:1200px;height:34px;background:var(--teal)}
.copyright{left:141px;top:9px;font-size:13px}
.social{top:11px;width:12px;height:12px;border-radius:50%;background:var(--white)}
svg .s{fill:none;stroke:var(--white);stroke-width:1.6;stroke-linecap:round;stroke-linejoin:round}
</style>
</head>
<body>
<div class="abs hero-visual" role="img" aria-label="Dark night city skyline with globe and network lines"></div>

<header class="abs site-header">
  <div class="abs brand">
    <span class="brand-dot"></span>
    <span class="brand-name">VENNATRA<br>MEDIA<br>INTELLIGENCE</span>
  </div>
  <div class="abs contact" style="left:734px">
    <span class="contact-icon"><svg width="13" height="13" viewBox="0 0 24 24"><path d="M6 2l4 4-2 3c1 3 4 6 7 7l3-2 4 4-3 4C10 22 2 14 2 5z" fill="#fff"/></svg></span>
    +1 555 014 7890
  </div>
  <div class="abs contact" style="left:900px">
    <span class="contact-icon"><svg width="14" height="11" viewBox="0 0 24 18"><rect x="1" y="1" width="22" height="16" class="s"/><path d="M1 1l11 9 11-9" class="s"/></svg></span>
    hello@vennatra.net
  </div>
  <nav class="nav">
    <a href="#" style="left:498px">Home</a>
    <a href="#" style="left:561px">Solutions</a>
    <a href="#" class="active" style="left:648px">Our Approach</a>
    <a href="#" style="left:760px">Our People</a>
    <a href="#" style="left:856px">Our Technology</a>
  </nav>
  <div class="abs sign-in">SIGN IN</div>
</header>

<h1 class="abs page-title">Our Approach</h1>
<p class="abs intro">We partner with in-market MMOs to source print, online, TV and radio content from 50+ geographies. Our multi-lingual analysts are domain experts with both in-depth market and industry expertise, and years of experience within media intelligence, PR and communications, and digital marketing.</p>

<section class="abs band light" style="top:302px;height:141px">
  <h2 class="abs row-label" style="top:42px;font-weight:400">Content<br>Sourcing</h2>
  <div class="abs item" style="left:293px;top:19px">
    <svg width="50" height="50" viewBox="0 0 50 50"><rect x="2" y="2" width="40" height="46" class="s"/><path d="M42 8h5v40H42M8 9h28v8H8zM8 22h14v18H8zM26 22h10M26 28h10M26 34h10M26 40h10" class="s"/></svg>
    Print<br>Global MNO Partners
  </div>
  <div class="abs item" style="left:505px;top:19px">
    <svg width="54" height="50" viewBox="0 0 54 50"><path d="M30 6l6-5 12 12-5 6M24 44l-6 5-12-12 5-6M20 30l14-12M16 34l-4 4M38 14l4-4" class="s"/><path d="M46 4l5-2M48 8l5 0M4 46l-3 3M6 42l-5 0" class="s"/></svg>
    Online<br>Web Crawlers
  </div>
  <div class="abs item" style="left:704px;top:19px">
    <svg width="52" height="50" viewBox="0 0 52 50"><path d="M2 20v10M7 15v20M12 20v10M17 10v30M22 4v42M26 1v48M30 4v42M35 10v30M40 18v14M45 22v6M50 20v10" class="s"/></svg>
    Tv &amp; Radio<br>Aggregation
  </div>
  <div class="abs item" style="left:904px;top:19px">
    <svg width="48" height="50" viewBox="0 0 48 50"><circle cx="10" cy="25" r="7" class="s"/><circle cx="38" cy="9" r="7" class="s"/><circle cx="38" cy="41" r="7" class="s"/><path d="M16 22l16-10M16 28l16 10" class="s"/></svg>
    Social Media<br>Platform
  </div>
</section>

<section class="abs band dark" style="top:450px;height:99px">
  <h2 class="abs row-label" style="top:22px;font-weight:400">Content<br>Collection</h2>
  <svg class="abs" style="left:539px;top:26px" width="106" height="48" viewBox="0 0 106 48"><ellipse cx="21" cy="8" rx="20" ry="6" class="s"/><path d="M1 8v32c0 8 40 8 40 0V8M1 19c0 8 40 8 40 0M1 30c0 8 40 8 40 0" class="s"/><ellipse cx="61" cy="21" rx="14" ry="4" class="s"/><path d="M47 21v22c0 6 28 6 28 0V21M47 29c0 6 28 6 28 0M47 36c0 6 28 6 28 0" class="s"/><ellipse cx="94" cy="31" rx="11" ry="3" class="s"/><path d="M83 31v13c0 4 22 4 22 0V31M83 36c0 4 22 4 22 0M83 40c0 4 22 4 22 0" class="s"/></svg>
  <p class="abs list" style="left:669px;top:30px;line-height:20px">Content Repository<br>&amp; Archive</p>
</section>

<section class="abs band dark" style="top:560px;height:99px">
  <h2 class="abs row-label" style="top:22px;font-weight:400">Content<br>Augmentation</h2>
  <svg class="abs" style="left:367px;top:24px" width="50" height="50" viewBox="0 0 50 50"><circle cx="19" cy="19" r="11" class="s"/><circle cx="19" cy="19" r="5" class="s"/><path d="M19 3v5M19 30v5M3 19h5M30 19h5M8 8l3 3M27 27l3 3M8 30l3-3M27 11l3-3" class="s"/><circle cx="37" cy="37" r="8" class="s"/><circle cx="37" cy="37" r="3" class="s"/><path d="M37 26v3M37 45v3M26 37h3M45 37h3" class="s"/></svg>
  <p class="abs list" style="left:433px;top:14px">AI Content Enhancement<br>Validation &amp; Summarisation Tools<br>Delivery Customisation</p>
  <svg class="abs" style="left:745px;top:24px" width="56" height="50" viewBox="0 0 56 50"><path d="M2 48v-8c0-5 6-7 11-9v-4c-3-2-4-6-4-10 0-7 4-11 9-11s9 4 9 11c0 4-1 8-4 10v4c5 2 11 4 11 9v8z" class="s"/><path d="M28 6c2-3 5-4 8-4 5 0 9 4 9 11 0 4-1 8-4 10v4c5 2 11 4 11 9v12H38" class="s"/></svg>
  <p class="abs list" style="left:815px;top:14px">Multi-lingual Team<br>Translation Summaries<br>Media Analysis</p>
</section>

<section class="abs band dark" style="top:669px;height:99px">
  <h2 class="abs row-label" style="top:22px;font-weight:400">Content<br>Delivery</h2>
  <svg class="abs" style="left:559px;top:23px" width="52" height="52" viewBox="0 0 52 52"><rect x="2" y="2" width="48" height="36" class="s"/><rect x="6" y="6" width="40" height="26" class="s"/><rect x="12" y="12" width="20" height="12" class="s"/><path d="M16 17h8M20 50h12M26 38v12M34 22l6 6-3 0 2 3" class="s"/></svg>
  <svg class="abs" style="left:632px;top:23px" width="50" height="50" viewBox="0 0 50 50"><path d="M2 20l23-16 23 16v28H2z" class="s"/><path d="M2 20l23 16 23-16M2 48l17-14M48 48L31 34M12 27V10h26v17M18 16h14M18 21h14" class="s"/></svg>
  <svg class="abs" style="left:702px;top:23px" width="88" height="54" viewBox="0 0 88 54"><path d="M14 2c-6 0-7 3-7 8v10c0 4-2 6-5 7 3 1 5 3 5 7v10c0 5 1 8 7 8M74 2c6 0 7 3 7 8v10c0 4 2 6 5 7-3 1-5 3-5 7v10c0 5-1 8-7 8" class="s"/><circle cx="30" cy="27" r="5" class="s"/><circle cx="44" cy="27" r="5" class="s"/><circle cx="58" cy="27" r="5" class="s"/></svg>
</section>

<footer class="abs site-footer">
  <p class="abs copyright">Copyright © 2019 Vennatra Media Intelligence. All Rights Reserved.</p>
  <span class="abs social" style="left:998px"></span>
  <span class="abs social" style="left:1021px"></span>
  <span class="abs social" style="left:1045px"></span>
</footer>
</body>
</html>
```